I need a newsletter that looks professional - our society colour is navy and white. I have also attached the LOOM newsletter which has a similar layout to what I want my one to look like. I have attached our logo as well to go on the front page with the title 'The Guild of Imaging Trainees Abroad Newsletter - Issue 1'.
I would like the newsletter to be 6 pages exactly like the LOOM newsletter please. I have attached the content of the newsletter in the order I want it in:

1) President of The GTA Column with portrait picture and President of the MVK Welcome Message (portrait picture and MVK logo) on the same page if possible
2) KOH content with group photo and KOH logo
3) Scanner Lounge content with logo and portrait photo
4) & 5) Harbourside Yearly Learning Summit with 5 photos if they all fit
6) PWN (with group photo) and MedPosts (with logo).

Please let me know if you need high quality versions of the logos.

Reason: Only one designer has submitted a design on the day of deadline - I would like to have a selection of designs to choose from please.

Target Market(s)

doctors

Industry/Entity Type

Training

Font styles to use
Serif

Colors
0c5ba6
3277b5
85abd2
cedeed
ffffff

Requirements
Must have
• the right colours to match our society - navys, light blues as selected.
• Must be easy on the eye and broken down in a way to make it readable - this is dependent on the layout
Nice to have
• slick, modern design fitting for radiologists

```html
<!DOCTYPE html>
<html lang="en">
<head>
<meta charset="utf-8">
<title>Harbourside Yearly Learning Summit 2017 – Newsletter Page 5</title>
<link rel="stylesheet" href="https://fonts.googleapis.com/css2?family=Noto+Serif:wght@400;700&display=swap">
<style>
  :root{
    --navy:#1b1d57;
    --navy-ink:#1e2266;
    --white:#ffffff;
    --ink:#1a1a1a;
    --label:rgba(40,42,100,.88);
  }
  *{margin:0;padding:0;box-sizing:border-box}
  html,body{width:927px;height:1200px;overflow:hidden;background:var(--navy)}
  body{position:relative;font-family:"Noto Serif",Georgia,serif;color:var(--ink)}
  .hero{position:absolute;left:24px;top:18px;width:878px;height:312px;display:flex}
  .hero-dock{width:436px;height:100%;background:linear-gradient(180deg,#3d4f66 0%,#6a5a50 45%,#3f4d5c 70%,#2d3a44 100%)}
  .hero-skyline{flex:1;height:100%;background:linear-gradient(180deg,#6fa6dc 0%,#9cc4ea 40%,#5d7a6c 62%,#2f4a62 78%,#3a3f4e 100%)}
  .hero-title{position:absolute;left:20px;top:6px;color:var(--white);font-weight:700;line-height:.92}
  .hero-title .words{font-size:50px;letter-spacing:.5px;display:block}
  .hero-title .year{font-size:92px;display:block;margin-top:4px}
  .sheet{position:absolute;left:24px;top:330px;width:878px;height:462px;background:var(--white)}
  .lede{position:absolute;left:140px;top:342px;width:648px;text-align:center;color:var(--navy-ink);font-weight:700;font-size:20.5px;line-height:23px}
  .col{position:absolute;width:268px;font-size:13.1px;line-height:15.6px;text-align:justify}
  .col p{margin-bottom:15.6px}
  .col p.tight{margin-bottom:6px}
  .c1{left:36px;top:429px}
  .c2{left:326px;top:429px}
  .c3{left:614px;top:429px}
  .photo-room{position:absolute;left:612px;top:606px;width:315px;height:320px;background:linear-gradient(180deg,#d9d4cc 0%,#8a6a4e 35%,#5b4636 60%,#3a3340 80%,#6b3a3a 100%)}
  .photo-workshop{position:absolute;left:0;top:792px;width:590px;height:408px;background:linear-gradient(120deg,#c8cdd4 0%,#e8e4e0 40%,#d6c6a8 65%,#8f8a86 100%)}
  .tag{position:absolute;left:0;top:878px;width:172px;height:37px;background:var(--label);color:var(--white);font-size:19px;line-height:37px;padding-left:20px}
  .day-two{position:absolute;left:606px;top:926px;width:296px;height:230px;background:var(--white)}
  .c4{left:614px;top:936px}
  .folio{position:absolute;right:25px;top:1176px;color:var(--white);font-size:12px}
  .folio b{font-weight:700}
</style>
</head>
<body>
  <header class="hero">
    <div class="hero-dock" role="img" aria-label="Photo of red-brick dock warehouses reflected in the harbour water"></div>
    <div class="hero-skyline" role="img" aria-label="Photo of the waterfront skyline with narrowboats moored in the dock"></div>
    <h1 class="hero-title"><span class="words">HARBOURSIDE<br>YEARLY<br>LEARNING<br>SUMMIT</span><span class="year">2017</span></h1>
  </header>

  <main>
    <div class="sheet"></div>
    <h2 class="lede">The 4th and 5th of May 2017 saw the Guild of Imaging Trainees Abroad hold our Yearly Learning Summit and AGM in sunny Portmere!</h2>

    <div class="col c1">
      <p>Our location was the Quayline Hotel in the attractive Marner Docks part of Portmere. In the foyer along with our sponsors Veltra and Norrow there were over 50 posters that our delegates had submitted with some well researched, creative and insightful topics on display.</p>
      <p>The delegates settled down to hear our first morning programme, with Dr. Owen Hartley from Clarivue opening the summit with a talk on learning from discrepancies, and Dr. Rajan Pillai on Cardiac CT. We also heard from Dr. Martin Cole on challenges and advances in breast radiology and Dr. Peter Ashby on some practical advice for trauma reporting.</p>
      <p>We had several interactive workshops that our delegates could sign up for</p>
    </div>

    <div class="col c2">
      <p>including abdomen and neck ultrasound demonstrations, and a state of the art fusion guided imaging and biopsy workshop with support from our friends at SUGP.</p>
      <p class="tight">These workshops would not be possible without our sponsors and volunteers offering their time and help for the day!</p>
      <p class="tight">Following a hot buffet lunch, our afternoon programme consisted of local consultants Dr. Neil Forbes on the topic of sport radiology and running a radiology service at the National Games, and from Dr. Anita Rowe delivering a SGAI lecture on abdominal trauma.</p>
      <p>We also heard from Dr. Vikram Shah from the Fenwick Centre on advances in neuroradiology and concluding the session we had current MVK President, Dr. Helen Marsh, talk about sustainable workforce planning.</p>
    </div>

    <div class="col c3">
      <p>In the evening we held our social event at Spice Quay on the Docks, which was a wonderful opportunity to chat with our delegates and find out about their interests and experiences in radiology and further afield.</p>
      <p>Some of our guests had travelled long distances to take part in our summit (as far as from Malta!) so thanks to all of you for making the journey!</p>
    </div>

    <div class="photo-room" role="img" aria-label="Photo of delegates seated at round tables in the summit hall"></div>
    <div class="photo-workshop" role="img" aria-label="Photo of a workshop tutor demonstrating an ultrasound machine"></div>
    <div class="tag">Workshops</div>

    <div class="day-two"></div>
    <div class="col c4">
      <p>Day 2 kicked off with our oral presentations from the delegates. We heard from 5 speakers who gave a short presentation, which was judged by our selected consultants.</p>
      <p>This category gives you the chance to improve your oral presentation skills in front of a receptive audience!</p>
      <p>Dr. Colin Baird and Dr. Stefan Weber spoke on post mortem CT and interventional radiology respectively, which brought us up to lunch.</p>
    </div>
  </main>

  <footer class="folio">The Guild of Imaging Trainees Abroad / Newsletter/ Issue 1 / <b>Page 5</b></footer>
</body>
</html>
```